Query Dale Penrose (Page Forge or Quiblo template)

Business Name?
Query Dale Penrose (QueryDalePenrose.com) Technically, this is the name of the web site. This is a venture, rather than a business. It is part of building my brand as an expert.

- What do you do?
I am a life strategist/coach (http://VelmoCraft.com/). This site will be a one-stop advice site, providing answers to real life challenges. The tagline is "life challenges, real solutions." It is a three step process: ASK-RECEIVE-ACHIEVE. It should, however, be FUN/ENGAGING (yet useful), rather than have a business/consultant feel. Approachable!

- How many pages do you need designed and code?
The site will have 7 sections:
Home (this is where I envision the introductory text, the ability for the user to submit their questions and they will be visible for all to see)
About Dale (my bio information/fascinating facts)
Dale's Notes (my blog-discussing general personal development topics and comments from readers)
Audio/Video (video tips and an audio player from chatwavecast.com that enables visitors to listen to my radio show/podcast)
Donations (this is where visitors can donate after they have had their questions answered. I am not attached to a specific vendor as long as it is NOT CoinTrove-perhaps Brimlo Pay. I need to have designated dollar increments that people can select-perhaps in $5 or $10 intervals)
Contact Dale (contact information and perhaps a TALKORA access button so that they can immediately contact me; it might be nice to have a chat room here for online chat, but I don't see this as vital)

- What is your industry?
Consulting/Professional Services

- Describe the target audience for your website design?
EVERYONE! I am going to becoming the "go-to guy" for when you are feeling stuck.

- What 3 things would you like to communicate to your audience through your website design?
Insightful, Engaging, Wise (& FUN, FUN, FUN!). This is not a traditional business site. I have one of those. It should be fun & cutting-edge.

- How is your company different from your competitors?
It is not what I do that is different. It is my approach. I believe that success is a product of conditioning. Rather than simply focusing on what you are doing (which is, naturally, important), you must also focus on who you are. "YOU" are the common denominator in all that you do!

- What website design styles do you like?
I tend to be attracted to fashion/photography/artist web sites. I love this Quiblo Zinbox design:
http://skinmarket.example/item/zinbox/full_screen_preview/7730518
I would love to have this style of menu navigation (these type of icons).

- What colors do you want to see in your website design?
I am completely open at this point (I have a couple of people working on a logo. It's not done yet. I now that it incorporates black & red, so, a black background might be nice). Naturally, this could influence it. I like "slick, sleek and cutting edge-something that will pop off the screen!

- What colors do you NOT want to see in your website design?
No restrictions as long as they are utilized in the appropriate balance/combination.

- What adjectives should best describe your website design?
Slick, sleek, cutting edge, cool, engaging, artistic

- What content must be included in the website design?
In addition to my logo and tagline : "life challenges, real solutions," I want to feature: ASK-RECEIVE-ACHIEVE somewhere.

- Do you have additional requirements or links you want to share?
The primary challenge (and unlike most web sites) is that the main section is user-driven. The user submits the questions and I respond after it is posted (unlike a typical blog where I post and users comment). In an ideal world I would like for the user to be able to select from one of six categories while submitting their question.(Relationships, Health/Body, Career/Work Life, Spirituality, Money/Finance, Other). Then, when the user selects their category, their question would be displayed in the appropriate section. The challenge with that is that I need to have at least some q&a displayed on the home page so that visitors get an immediate sense of what I am doing. I want to have the ability to also response to submitted questions via video should I choose to do so. I want visitors to be able to share postings/my responses on Friendlane, Chirpex, etc.

Page Forge has 3 templates that enable this q&a capability, but they are very unattractive in their design (like tech help forums-EW!) and they seem to require users to create their own profile page, etc. I don't see that as necessary. I don't know what can be modified, turned off, etc.
http://toppfhelpdesk.example/the-best-pageforge-themes-for-creating-qa-websites/
Updates

First of all: Thank you for bringing your creative gifts/talents/expertise to my challenge!

I assume it is sometimes challenging having to fill space without the actual words, so I have attached some documents that I am hoping will be helpful.

Logo-I didn't know what type of file you need, so I have attached .jpg, .pns, .eps
Pictures-I will be having some professional pics taken, but in the interim, I have attached 3 that can be used. I like the one with the hat as the main pic.
Documents:
-Query Dale Penrose Home-this is the text for the introduction that precedes the Q&A section on the home page
-About Dale/25 Random Facts-for the About Dale section.
-Dale's Notes-I have attached some blog entries for this section

If you have any questions, please do not hesitate to contact me. Thanks, again, for joining me. Please know that I work without a great many people who are in need of good designers for their projects/businesses. I will happily direct them to the people with the best talents when we are through. I want this to be a win-win for all of us!

Hello Designers!

I wanted to take a moment to stress that I really want something "cutting-edge." I am NOT looking for something that is traditional (and especially not something that has a corporate/consultant flavor). I want FUN. As I have stated-think artist/fashion/creative. I referred you all to the Quiblo design because I like that look at feel. I like the navigation icons and the navigation of that template. Because I like cutting edge, please refrain from the use of stock photography or clip art.

I really need for users to know immediately what this site is all about-right from the home page, without having to navigate around. I have always envisioned q&a being on the home page. If this cannot work, I am open to alternatives, as long as it is clear what the site is about. 

I attached the logo, the intro text and some text for other sections for a reason. Please use it! This will enable me to truly envision what you see and how this should all blend together. Thank you so much.

If I can provide any additional information or assistance, please do not hesitate to contact me. 

Hello Designers:

I had a slight modification made to the logo (a little more white space-think you'll like it better). I deleted the old files and uploaded new attachments of the revised logo. I wasn't sure which file format you prefer to work with so I included a few!

Please do not hesitate to ask any questions should they arise. Thanks for your hard work.

Dale

Reason: Since many seem to be pressed to participate due to competing schedules, I am adding a couple more days. Only a couple! Before submitting a design, please pay close attention to my brief. I must see how the home page intro and the q&a will be incorporated and displayed. To all who choose to contribute their gifts and talents to this challenge, I really appreciate it. Thanks! Dale

Target Market(s)

EVERYONE! Yes, the world!

Industry/Entity Type

Building

Requirements
Must have
• There can be no compromise in the user-driven question and answer capability (where the questions are clearly displayed for all to see). This is the point of the entire site, so without it, there is no point!

All have my desired sections have already been detailed above.
Should not have
• I do not want this site to look like a typical coaching or corporate consulting site. Fun, engaging, cutting edge & forward thinking!

```html
<!DOCTYPE html>
<html lang="en">
<head>
<meta charset="utf-8">
<title>Query Dale Penrose</title>
<link rel="stylesheet" href="https://fonts.googleapis.com/css2?family=Open+Sans:wght@400;600;700&family=Play:wght@400;700&family=Ubuntu:wght@400;500&display=swap">
<style>
:root{
  --black:#0d0d0d;
  --ink:#222;
  --body:#444;
  --navy:#0c1a4a;
  --orange:#f28a10;
  --page:#e6e6e6;
  --card:#fff;
  --rule:#dcdcdc;
  --tab-grey:#5a5a5a;
  --bar:#efefef;
}
*{box-sizing:border-box;margin:0;padding:0}
html,body{width:821px;height:1200px;overflow:hidden}
body{background:var(--page);font-family:"Open Sans",sans-serif;color:var(--ink);position:relative}
.abs{position:absolute}
.topbar{left:0;top:0;width:821px;height:40px;background:linear-gradient(#1c1c1c,#000)}
.account{right:45px;top:14px;font-size:10.5px;color:#9a9a9a;letter-spacing:.2px}
.account span{margin:0 8px;color:#666}
.masthead{left:0;top:40px;width:821px;height:83px;background:linear-gradient(#f7f7f7,#d9d9d9)}
.brand-mark{left:36px;top:59px;width:42px;height:42px;border-radius:50%;background:#1a4fc7;box-shadow:0 2px 4px rgba(0,0,0,.3)}
.brand-name{left:86px;top:71px;font-family:"Ubuntu",sans-serif;font-size:19px;font-weight:500;color:#1d1d1d;letter-spacing:.2px}
.nav-icon{top:69px;width:31px;height:31px;border-radius:50%;background:var(--black);display:flex;align-items:center;justify-content:center;color:#fff;font:700 13px "Open Sans",sans-serif;box-shadow:0 2px 3px rgba(0,0,0,.35)}
.hero-band{left:0;top:123px;width:821px;height:321px;background:linear-gradient(#2d2d2d,#1a1a1a)}
.hero-frame{left:26px;top:140px;width:769px;height:282px;background:#fff}
.hero-photo{left:33px;top:147px;width:519px;height:268px;background:linear-gradient(135deg,#eef2f6,#d9dfe6 55%,#c5ccd4)}
.hero-panel{left:560px;top:147px;width:225px;height:268px;background:linear-gradient(#e8e8e8,#cfcfcf);text-align:center;padding-top:48px}
.hero-panel p{font-family:"Ubuntu",sans-serif;font-size:34px;line-height:48px;color:var(--navy)}
.slider-dots{left:739px;top:403px;display:flex;gap:2px}
.slider-dots i{width:6px;height:6px;background:#111;display:block}
.card{background:var(--card);box-shadow:0 3px 6px rgba(0,0,0,.12)}
.side-head{background:var(--black);color:#fff;font-family:"Play",sans-serif;font-size:16px;padding:7px 0 0 14px}
.category{left:25px;top:455px;width:210px;height:239px}
.category .side-head{margin:5px 5px 0;height:33px}
.category ul{list-style:none;margin:6px 0 0}
.category li{height:31px;border-bottom:1px solid #ececec;display:flex;align-items:center;font-size:12px;padding-left:24px;gap:12px}
.category li:last-child{border:0}
.category svg{width:20px;height:16px}
.testimonials{left:25px;top:704px;width:210px;height:395px}
.testimonials .side-head{margin:6px 5px 0;height:34px}
.quote{position:absolute;left:11px;width:192px}
.quote .thumb{position:absolute;left:0;top:0;width:45px;height:38px;background:linear-gradient(#6aa0d8,#2c5d96)}
.quote p{margin-left:52px;font-size:9.5px;line-height:13px;color:#222}
.quote b{display:block;margin:5px 0 0 52px;font-size:9.5px;font-weight:400}
.viewall{position:absolute;left:12px;top:360px;width:186px;height:18px;background:var(--bar);font-size:10.5px;text-align:right;padding:2px 14px 0 0}
.main{left:241px;top:455px;width:562px;height:644px}
.tabs{position:absolute;left:7px;top:6px;width:548px;height:36px;background:var(--black)}
.tab{position:absolute;top:3px;height:33px;font-family:"Play",sans-serif;font-size:15px;color:#ddd;padding:8px 0 0 16px;border-radius:3px 3px 0 0}
.tab.on{background:#1d1d1d;color:#fff;left:0;width:106px;padding-left:14px}
.tab.off{background:var(--tab-grey)}
.qa{position:absolute;left:0;width:562px}
.bubble{position:absolute;width:50px;height:38px}
.qa h2{font-family:"Ubuntu",sans-serif;font-weight:400;font-size:15px;color:#1a1a1a}
.qa p{font-size:9px;line-height:14px;color:var(--body);margin-top:5px;width:460px}
.qa .meta{font-size:9px;margin-top:9px;display:flex;align-items:center;gap:5px}
.qa .meta b{font-weight:700}
.qa .meta i{width:12px;height:7px;border-radius:4px;background:#111;display:inline-block;margin-left:10px}
.rule{position:absolute;left:14px;width:532px;height:1px;background:var(--rule)}
.pager{position:absolute;left:17px;top:609px;width:521px;height:18px;background:var(--bar);font-size:10px;padding:3px 0 0 10px}
.pager span{position:absolute;right:10px;top:2px;word-spacing:5px}
.pager span em{font-style:normal;background:#ddd;padding:0 3px}
.footer{left:0;top:1122px;width:821px;height:78px;background:#000;color:#fff;font-family:"Play",sans-serif;font-size:11px}
.footer .copy{position:absolute;left:29px;top:25px}
.footer nav{position:absolute;right:26px;top:25px}
.footer nav span{margin:0 4px;color:#bbb}
</style>
</head>
<body>
<div class="abs topbar"></div>
<div class="abs account">LOGIN<span>|</span>SIGN UP</div>

<header class="abs masthead"></header>
<div class="abs brand-mark"></div>
<div class="abs brand-name">QUERY DALE PENROSE</div>

<div class="abs nav-icon" style="left:449px"><svg width="13" height="13" viewBox="0 0 12 12"><path d="M6 1L1 6h2v5h2.5V8h1v3H9V6h2z" fill="#fff"/></svg></div>
<div class="abs nav-icon" style="left:496px"><svg width="12" height="12" viewBox="0 0 12 12"><path d="M1 5h6V2l4 4-4 4V7H1z" fill="#fff"/></svg></div>
<div class="abs nav-icon" style="left:543px">2</div>
<div class="abs nav-icon" style="left:589px"><svg width="13" height="12" viewBox="0 0 13 12"><path d="M1 4h3l4-3v10L4 8H1z" fill="#fff"/><path d="M10 3.5q2 2.5 0 5" stroke="#fff" fill="none" stroke-width="1.3"/></svg></div>
<div class="abs nav-icon" style="left:635px"><svg width="12" height="12" viewBox="0 0 12 12"><path d="M2 1h2v10H2zM11 1v10L4.5 6z" fill="#fff"/></svg></div>
<div class="abs nav-icon" style="left:682px"><svg width="14" height="12" viewBox="0 0 14 12"><path d="M5 1h2v4h3L6 9 2 5h3z" fill="#fff"/><path d="M1 9h12v2H1z" fill="#fff"/></svg></div>
<div class="abs nav-icon" style="left:729px"><svg width="12" height="13" viewBox="0 0 12 13"><path d="M3 1l2 3-1.3 1.3q1 2.7 3.5 4L8.5 8l3 2-1.5 2.5Q4 12 1.5 3z" fill="#fff"/></svg></div>

<section class="abs hero-band"></section>
<div class="abs hero-frame"></div>
<div class="abs hero-photo" role="img" aria-label="Photo of a woman lying on a bright floor working on a laptop"></div>
<div class="abs hero-panel"><p>ASK</p><p>RECEIVE</p><p>ACHIEVE</p></div>
<div class="abs slider-dots"><i></i><i></i><i></i><i></i><i></i></div>

<aside class="abs card category">
  <div class="side-head">Our Category</div>
  <ul>
    <li><svg viewBox="0 0 20 16"><path d="M10 15L2.5 7.5A4 4 0 0 1 10 3a4 4 0 0 1 7.5 4.5z" fill="#e3231c"/></svg>Relationships</li>
    <li><svg viewBox="0 0 20 16"><circle cx="10" cy="5" r="4" fill="#b5793d"/><path d="M3 16q0-6 7-6t7 6z" fill="#3a8a2a"/></svg>Health/Body</li>
    <li><svg viewBox="0 0 20 16"><circle cx="10" cy="8" r="7" fill="#4cae34"/><circle cx="10" cy="8" r="3.5" fill="#fff"/></svg>Career/Work Life</li>
    <li><svg viewBox="0 0 20 16"><circle cx="10" cy="6" r="5.5" fill="#f4a31c"/><rect x="7.5" y="11" width="5" height="4" fill="#3d86c9"/></svg>Spirituality</li>
    <li><svg viewBox="0 0 20 16"><rect x="1" y="3" width="18" height="11" rx="1" fill="#3e78b8"/><rect x="1" y="6" width="18" height="2" fill="#cfe0f2"/></svg>Money/Finance</li>
    <li><svg viewBox="0 0 20 16"><path d="M1 8l8-7v4h10v6H9v4z" fill="#a554b8"/></svg>Other</li>
  </ul>
</aside>

<aside class="abs card testimonials">
  <div class="side-head">Testimonials</div>
  <div class="quote" style="top:52px"><div class="thumb" role="img" aria-label="Photo of a card and keyboard"></div><p>E-Commerce is a major progress in technology that has changed the way in which the customers.</p><b>READ MORE</b></div>
  <div class="quote" style="top:124px"><div class="thumb" role="img" aria-label="Photo of a child with a laptop outdoors"></div><p>E-Commerce is a major progress in technology that has changed the way in which the customers.</p><b>READ MORE</b></div>
  <div class="quote" style="top:195px"><div class="thumb" style="background:linear-gradient(#c9c9c9,#6a4a3a)" role="img" aria-label="Photo of a man at an office desk"></div><p>E-Commerce is a major progress in technology that has changed the way in which the customers.</p><b>READ MORE</b></div>
  <div class="quote" style="top:266px"><div class="thumb" style="background:linear-gradient(#8a5a3a,#3a2418)" role="img" aria-label="Photo of a person thinking hard"></div><p>When considering advanced web development project, finding the right answers to the hard questions is a challenge for any firm</p><b>READ MORE</b></div>
  <div class="viewall">View all</div>
</aside>

<main class="abs card main">
  <div class="tabs">
    <div class="tab on">Recent Q/A</div>
    <div class="tab off" style="left:113px;width:67px">Blogs</div>
    <div class="tab off" style="left:188px;width:100px">Comments</div>
  </div>

  <article class="qa" style="top:58px">
    <svg class="bubble" style="left:14px;top:14px" viewBox="0 0 50 38"><ellipse cx="25" cy="14" rx="24" ry="13" fill="var(--orange)"/><path d="M18 24l12 2-4 10z" fill="var(--orange)"/></svg>
    <div style="margin-left:76px">
      <h2>Can we actual art therapist or something in other related field ?</h2>
      <p>E-Commerce is a major progress in technology that has changed the way in which the customers now purchase information, products and the services. It's the new way of providing an opportunity to make your products and services available in the global market 24 hours a day through Internet<br>Brightmoor WebWorks is specialized in handling advanced web projects and the ongoing projects that require permanent maintenance and support.</p>
      <div class="meta">Asked by <b>Author Name</b><i></i><b>688 views</b></div>
    </div>
  </article>
  <div class="rule" style="top:183px"></div>

  <article class="qa" style="top:196px">
    <svg class="bubble" style="left:12px;top:14px" viewBox="0 0 50 38"><ellipse cx="25" cy="14" rx="24" ry="13" fill="var(--orange)"/><path d="M18 24l12 2-4 10z" fill="var(--orange)"/></svg>
    <div style="margin-left:74px">
      <h2>Why Brightmoor WebWorks to specialize in advanced projects ?</h2>
      <p>E-Commerce is a major progress in technology that has changed the way in which the customers now purchase information, products and the services. It's the new way of providing an opportunity to make your products and services available in the global market 24 hours a day through Internet<br>Brightmoor WebWorks is specialized in handling advanced web projects and the ongoing projects that require permanent maintenance and support.</p>
      <div class="meta">Asked by <b>Author Name</b><i></i><b>688 views</b></div>
    </div>
  </article>
  <div class="rule" style="top:318px"></div>

  <article class="qa" style="top:333px">
    <svg class="bubble" style="left:5px;top:14px" viewBox="0 0 50 38"><ellipse cx="25" cy="14" rx="24" ry="13" fill="var(--orange)"/><path d="M18 24l12 2-4 10z" fill="var(--orange)"/></svg>
    <div style="margin-left:66px">
      <h2>Can we actual art therapist or something in other related field ?</h2>
      <p>E-Commerce is a major progress in technology that has changed the way in which the customers now purchase information, products and the services. It's the new way of providing an opportunity to make your products and services available in the global market 24 hours a day through Internet<br>Brightmoor WebWorks is specialized in handling advanced web projects and the ongoing projects that require permanent maintenance and support.</p>
      <div class="meta">Asked by <b>Author Name</b><i></i><b>688 views</b></div>
    </div>
  </article>
  <div class="rule" style="top:461px"></div>

  <article class="qa" style="top:477px">
    <svg class="bubble" style="left:17px;top:14px" viewBox="0 0 50 38"><ellipse cx="25" cy="14" rx="24" ry="13" fill="var(--orange)"/><path d="M18 24l12 2-4 10z" fill="var(--orange)"/></svg>
    <div style="margin-left:78px">
      <h2>Can we actual art therapist or something in other related field ?</h2>
      <p>E-Commerce is a major progress in technology that has changed the way in which the customers now purchase information, products and the services. It's the new way of providing an opportunity to make your products and services available in the global market 24 hours a day through Internet<br>Brightmoor WebWorks is specialized in handling advanced web projects and the ongoing projects that require permanent maintenance and support.</p>
      <div class="meta">Asked by <b>Author Name</b><i></i><b>688 views</b></div>
    </div>
  </article>

  <div class="pager">Pages<span><em>1</em> 2 3 4 5</span></div>
</main>

<footer class="abs footer">
  <div class="copy">© 2012 Company Name&nbsp; All right reserved</div>
  <nav>Home<span>|</span>About Dale<span>|</span>Dale's Notes<span>|</span>Audio / Video<span>|</span>Donations<span>|</span>Contact</nav>
</footer>
</body>
</html>
```